New Bicycle shop business card

Hi!
I'm looking for a business card for my new proffesional bike mechanics shop. This shop is only for fixing broken bikes and not selling bikes.
Peferbly a modern and sleek and modern design.
Colors: black, grey, red, white
Information:
Name: Rijwielwerkplaats Vanhoutte
Shop owner: Bart Vanhoutte & Marieke Segers
Website: www.rijwielwerkplaats-vanhoutte.be
Email: info@rijwielwerkplaats-vanhoutte.be
Phone number: +32471902368
Street adres: Kerkweg 46
9940 Bellebeke
Slogan/shop information: Herstellingen van alle merken.
Logo: see files.
Target Market(s)
People who seek a mechanic to fix or upgrade their bikes.
Contact Information for Business Card
Information:
Website: info@rijwielwerkplaats-vanhoutte.be
9940 Bellebeke
Logo: see files.

```html
<!DOCTYPE html>
<html lang="nl">
<head>
<meta charset="utf-8">
<title>Rijwielwerkplaats Vanhoutte – Visitekaartje</title>
<link rel="stylesheet" href="https://fonts.googleapis.com/css2?family=Roboto:wght@400;500;700&display=swap">
<style>
  :root {
    --backdrop: #d9d9d9;
    --card: #ffffff;
    --card-shade: #f3f3f3;
    --ink: #1c1c1c;
    --ink-soft: #3a3a3a;
    --red: #d62839;
    --grey: #9a9da1;
    --rule: #e2e2e2;
  }
  * { box-sizing: border-box; margin: 0; padding: 0; }
  html, body { width: 1200px; height: 852px; overflow: hidden; }
  body {
    background: var(--backdrop);
    font-family: "Roboto", Arial, sans-serif;
    color: var(--ink);
    position: relative;
  }
  .card {
    position: absolute;
    width: 500px;
    height: 290px;
    background: var(--card);
    border-radius: 18px;
    overflow: hidden;
    box-shadow: 0 14px 30px rgba(0,0,0,.18);
  }
  .card--front { left: 90px; top: 150px; }
  .card--back  { left: 610px; top: 412px; }

  /* brand name (set as plain text) */
  .brand {
    display: flex;
    align-items: center;
    gap: 10px;
  }
  .brand__mark {
    width: 16px; height: 16px;
    background: var(--red);
    flex: none;
  }
  .brand__name {
    font-weight: 700;
    font-size: 19px;
    letter-spacing: 1px;
    text-transform: uppercase;
    line-height: 1.15;
    color: var(--ink);
  }

  /* front */
  .front__brand {
    position: absolute;
    left: 0; right: 0; top: 86px;
    justify-content: center;
  }
  .front__brand .brand__name { font-size: 22px; text-align: left; }
  .front__tagline {
    position: absolute;
    left: 0; right: 0; top: 196px;
    display: flex; align-items: center; justify-content: center; gap: 14px;
    font-size: 13px; color: var(--ink-soft);
  }
  .front__tagline::before, .front__tagline::after {
    content: ""; width: 44px; height: 2px; background: var(--red);
  }
  .front__band {
    position: absolute; left: 0; right: 0; bottom: 0; height: 10px;
    display: flex;
  }
  .front__band span:first-child { flex: 1; background: var(--red); }
  .front__band span:last-child { flex: 1; background: var(--grey); }

  /* back */
  .back__logo-side {
    position: absolute; left: 0; top: 0; bottom: 0; width: 250px;
    display: flex; align-items: center; justify-content: center;
    padding: 0 18px;
  }
  .back__logo-side .brand__name { font-size: 17px; }
  .back__info-side {
    position: absolute; left: 250px; top: 0; right: 0; bottom: 0;
    background: var(--card-shade);
    border-left: 1px solid var(--rule);
    padding: 56px 14px 0 22px;
  }
  .person__name {
    font-weight: 700; font-size: 19px; letter-spacing: .5px;
    text-transform: uppercase; color: var(--red);
  }
  .person__role { font-size: 12px; color: var(--ink-soft); margin-top: 2px; }
  .contact { list-style: none; margin-top: 14px; }
  .contact li {
    display: flex; align-items: center; gap: 8px;
    font-size: 11px; color: var(--ink-soft); line-height: 19px;
    white-space: nowrap;
  }
  .contact svg { width: 11px; height: 11px; flex: none; fill: var(--red); }
  .back__tab {
    position: absolute; right: 0; bottom: 0;
    width: 232px; height: 40px;
    background: var(--red);
    border-top-left-radius: 12px;
    color: #fff; font-size: 12.5px;
    display: flex; align-items: center; justify-content: center;
  }
</style>
</head>
<body>

  <section class="card card--front" aria-label="Voorkant visitekaartje">
    <div class="brand front__brand">
      <span class="brand__mark"></span>
      <span class="brand__name">Rijwielwerkplaats<br>Vanhoutte</span>
    </div>
    <p class="front__tagline">Herstellingen van alle merken</p>
    <div class="front__band"><span></span><span></span></div>
  </section>

  <section class="card card--back" aria-label="Achterkant visitekaartje">
    <div class="back__logo-side">
      <div class="brand">
        <span class="brand__mark"></span>
        <span class="brand__name">Rijwielwerkplaats<br>Vanhoutte</span>
      </div>
    </div>
    <div class="back__info-side">
      <h1 class="person__name">Marieke Segers</h1>
      <p class="person__role">Owner</p>
      <ul class="contact">
        <li>
          <svg viewBox="0 0 24 24" aria-hidden="true"><path d="M6.6 10.8a15.1 15.1 0 0 0 6.6 6.6l2.2-2.2c.3-.3.7-.4 1-.2 1.1.4 2.3.6 3.6.6.6 0 1 .4 1 1V20c0 .6-.4 1-1 1A17 17 0 0 1 3 4c0-.6.4-1 1-1h3.5c.6 0 1 .4 1 1 0 1.3.2 2.5.6 3.6.1.3 0 .7-.2 1z"/></svg>
          +32471902368
        </li>
        <li>
          <svg viewBox="0 0 24 24" aria-hidden="true"><path d="M12 2a10 10 0 1 0 0 20 10 10 0 0 0 0-20zm6.9 6h-2.9a15.7 15.7 0 0 0-1.4-3.6A8 8 0 0 1 18.9 8zM12 4c.8 1.2 1.5 2.5 1.9 4h-3.8c.4-1.4 1.1-2.8 1.9-4zM4.3 14a8 8 0 0 1 0-4h3.4a16.5 16.5 0 0 0 0 4zm.8 2h2.9c.3 1.3.8 2.5 1.4 3.6A8 8 0 0 1 5.1 16zM8 8H5.1a8 8 0 0 1 4.3-3.6C8.8 5.5 8.3 6.7 8 8zm4 12c-.8-1.2-1.5-2.5-1.9-4h3.8c-.4 1.4-1.1 2.8-1.9 4zm2.3-6H9.7a14.7 14.7 0 0 1 0-4h4.6a14.7 14.7 0 0 1 0 4zm.3 5.6c.6-1.1 1.1-2.3 1.4-3.6h2.9a8 8 0 0 1-4.3 3.6zm1.7-5.6a16.5 16.5 0 0 0 0-4h3.4a8 8 0 0 1 0 4z"/></svg>
          www.rijwielwerkplaats-vanhoutte.be
        </li>
        <li>
          <svg viewBox="0 0 24 24" aria-hidden="true"><path d="M2 5h20v14H2zm2 2v.5l8 5 8-5V7zm0 2.8V17h16V9.8l-8 5z"/></svg>
          info@rijwielwerkplaats-vanhoutte.be
        </li>
        <li>
          <svg viewBox="0 0 24 24" aria-hidden="true"><path d="M12 2a7 7 0 0 0-7 7c0 5.2 7 13 7 13s7-7.8 7-13a7 7 0 0 0-7-7zm0 9.5A2.5 2.5 0 1 1 12 6.5a2.5 2.5 0 0 1 0 5z"/></svg>
          Kerkweg 46 9940 Bellebeke
        </li>
      </ul>
    </div>
    <div class="back__tab">Herstellingen van alle merken</div>
  </section>

</body>
</html>
```